Advanced Therapeutic Massage Therapist

I need a business card advertising my massage services as an advanced therapeutic massage therapist. I offer advanced therapeutic massage, swedish and deep tissue. I want to create a simple, professional and feminine card. I like bright colours and creativity.

I prefer a bold and experimental approach rather than something status-quo. A card to suggest therapeutic healing through dynamic massage. Motifs, shapes or layout which suggest movement and flow.
Updates

Target Market(s)

Everybody!

Industry/Entity Type

Health And Wellness

Contact Information for Business Card

The card should include:
My name, logo, services offered and my contact details.

Sláine Dunleavy
Massage Therapist

- Swedish - Deep Tissue - Advanced Therapeutic

Phone: (+353) 87 216 4093
Email: regenerate@slainedunleavy-example.com
Website: www.slainedunlevy-example.com

Font styles to use
Serif
Sans Serif
Decorative
Script

Colors

Designer to choose colors to be used in the design.

Requirements
Must have
• An example may contain something like this, yet concise:
• "Sláine Dunleavy
• Massage Therapist
• - Swedish - Deep Tissue - Advanced Therapeutic"
Nice to have
• This sentence is optional:
• Imagery such as a logo or symbol. I have attached a file containing a logo I had produced however the name is incorrect now as it is "Sláine" not "Nelly". It could be edited to change it to Sláine.
• I have sent the file as .psd .jpg. .pdf and .png
• I like when the card conveys energy, movement, pressure points, flow etc.
• I just like the designer to follow their own style and ideas. I like bright colours but must have a lot of a base colour to offset it. I really prefer them to follow their own inspiration. That is my preference.
Should not have
• Pine trees, non-native trees to Britain and Ireland, exotic flowers or animals that are not native to Britain and Ireland.
• I don't like brown as the background colour of the card.
• The cars shouldn't look like a wedding invitation i.e too many floral type designs.

```html
<!DOCTYPE html>
<html lang="en">
<head>
<meta charset="utf-8">
<title>Sláine Dunleavy – Massage Therapist Business Card</title>
<link rel="stylesheet" href="https://fonts.googleapis.com/css2?family=Kaushan+Script&family=Open+Sans:wght@400;600&display=swap">
<style>
  :root {
    --backdrop: #3b3532;
    --card: #0d0c0c;
    --gold: #d99a3a;
    --gold-deep: #a96e1f;
    --mint: #bfe6dc;
    --mint-soft: #8fcfc0;
    --text-light: #f2f2f2;
    --tagline: #9fd8c8;
  }
  * { box-sizing: border-box; margin: 0; padding: 0; }
  html, body {
    width: 1200px; height: 900px; overflow: hidden;
    background: var(--backdrop);
    font-family: "Open Sans", Arial, sans-serif;
  }
  .canvas {
    position: relative; width: 1200px; height: 900px;
    display: flex; align-items: center; justify-content: center; gap: 40px;
  }
  .card {
    position: relative; width: 520px; height: 300px;
    background: var(--card);
    box-shadow: 0 10px 30px rgba(0,0,0,.45);
    overflow: hidden;
  }
  .logo-mark {
    position: absolute; border-radius: 50%;
    background: radial-gradient(circle at 45% 40%, var(--mint) 0%, var(--mint-soft) 70%, #7bb9a8 100%);
    box-shadow: 0 0 0 6px var(--card), 0 0 0 9px var(--gold-deep);
  }
  .card-front .logo-mark { left: 50px; top: 58px; width: 150px; height: 150px; }
  .identity { position: absolute; left: 240px; top: 62px; }
  .name {
    font-family: "Kaushan Script", cursive;
    color: var(--gold); font-size: 30px; font-weight: 400; line-height: 1.1;
  }
  .role { color: var(--text-light); font-size: 15px; margin-top: 2px; }
  .contact { list-style: none; margin-top: 34px; }
  .contact li {
    display: flex; align-items: center; gap: 8px;
    color: var(--text-light); font-size: 15px; line-height: 1.55;
  }
  .contact svg { width: 13px; height: 13px; flex: none; fill: var(--gold); }
  .services {
    position: absolute; left: 40px; bottom: 30px;
    list-style: none; display: flex; gap: 22px;
  }
  .services li {
    display: flex; align-items: center; gap: 10px;
    color: var(--text-light); font-size: 16px;
  }
  .services li::before {
    content: ""; width: 9px; height: 9px; border-radius: 50%; background: var(--gold);
  }
  .card-back .logo-mark { left: 205px; top: 42px; width: 110px; height: 110px; }
  .tagline {
    position: absolute; left: 60px; right: 60px; top: 190px;
    text-align: center; color: var(--tagline); font-size: 14px; line-height: 1.45;
  }
</style>
</head>
<body>
<main class="canvas">
  <section class="card card-front">
    <div class="logo-mark" role="img" aria-label="Logo: gold ornamental tree in a mint circle"></div>
    <div class="identity">
      <h1 class="name">Sláine Dunleavy</h1>
      <p class="role">Massage Therapist</p>
      <ul class="contact">
        <li>
          <svg viewBox="0 0 24 24" aria-hidden="true"><path d="M6.6 10.8a15.1 15.1 0 0 0 6.6 6.6l2.2-2.2a1 1 0 0 1 1-.25 11.4 11.4 0 0 0 3.6.57 1 1 0 0 1 1 1V20a1 1 0 0 1-1 1A17 17 0 0 1 3 4a1 1 0 0 1 1-1h3.5a1 1 0 0 1 1 1c0 1.25.2 2.45.57 3.57a1 1 0 0 1-.25 1z"/></svg>
          (+353) 87 216 4093
        </li>
        <li>
          <svg viewBox="0 0 24 24" aria-hidden="true"><path d="M2 5h20v14H2z M2 5l10 8 10-8" fill="var(--gold)"/><path d="M3 6l9 7 9-7" fill="none" stroke="#0d0c0c" stroke-width="1.6"/></svg>
          slainemassage@example.com
        </li>
      </ul>
    </div>
    <ul class="services">
      <li>Swedish</li>
      <li>Deep Tissue</li>
      <li>Advanced Therapeutic</li>
    </ul>
  </section>

  <section class="card card-back">
    <div class="logo-mark" role="img" aria-label="Logo: gold ornamental tree in a mint circle"></div>
    <p class="tagline">HTCB qualified specialising in advanced therapeutic and<br>deep tissue massage</p>
  </section>
</main>
</body>
</html>
```